Existing Website Requiring new Pages

I have an existing word press website that was built using elementor.
Website: www.tallowcrestcare.com.au
I require the Vacancies page (https://www.tallowcrestcare.com.au/vacancies/) to be modified to display our new properties along with minor tweaks to how the information is presented.
The vacancies to be displayed are the exactly the same as those that are located on the homepage of QMR website (https://qmr.org.au/)
The new pages that link off the Vacancies tab will require custom design.
There are roughly 8 pages/properties to be incorporated. i wish for the design to be very similar to that displayed in the following link; https://www.polunda.com.au/vacancies/merrylands
Along with this the back end has not been updated for the last 3 years so it also requires some maintenance.
Website is in the disability industry and the custom pages will display information relative to Property Vacancies.
I have attached a ZIP file with some design guides, the information for each of the properties (which will need to be modified to show our business name Tallowcrest Care) and the example of how it is to look based off the Polunda website.
If you guys have any suggestions or ideas on how to make this more presentable or possible i'm open to your ideas.
Target Market(s)
People looking for SDA properties custom built for people with a disability
Industry/Entity Type
Disability
Coding
Coded - Design and coding required
Number of Pages Required
5+ page

```html
<!DOCTYPE html>
<html lang="en">
<head>
<meta charset="utf-8">
<title>Vacancies – Tallowcrest Care</title>
<link rel="stylesheet" href="https://fonts.googleapis.com/css2?family=Montserrat:wght@400;500;600;700&display=swap">
<style>
:root{
  --coral:#f7997b;
  --teal:#1fc9a8;
  --magenta:#c0208f;
  --ink:#2b2b2b;
  --nav:#333333;
  --muted:#6f6f6f;
  --link:#7c7192;
  --pink:#e0457f;
  --blue:#2a8de0;
  --rule:#e4e4e4;
  --bar:#1f1f1f;
  --white:#ffffff;
}
*{margin:0;padding:0;box-sizing:border-box}
html,body{width:1200px;height:2198px;overflow:hidden;background:var(--white)}
body{position:relative;font-family:"Montserrat",sans-serif;color:var(--ink)}

.site-header{position:absolute;left:0;top:0;width:1200px;height:125px;background:var(--white)}
.brand{position:absolute;left:116px;top:44px;display:flex;align-items:center;gap:8px}
.brand-dot{width:26px;height:26px;border-radius:50%;background:var(--coral)}
.brand-name{font-size:17px;font-weight:700;color:var(--magenta);letter-spacing:.3px}
.main-nav{position:absolute;top:57px;left:562px;display:flex;gap:0;font-size:10.5px;font-weight:700;letter-spacing:.4px;color:var(--nav)}
.main-nav span{position:absolute;white-space:nowrap}
.main-nav .active{color:var(--coral)}

.hero{position:absolute;left:0;top:125px;width:1200px;height:542px;overflow:hidden}
.hero-photo{position:absolute;inset:0;background:linear-gradient(100deg,#cdbfae 0%,#a88d6f 40%,#6e5a48 70%,#3f3730 100%)}
.hero-shape{position:absolute;inset:0}
.hero-title{position:absolute;left:111px;top:358px;font-size:43px;font-weight:600;color:var(--white);text-shadow:0 2px 6px rgba(0,0,0,.18)}
.hero-rule{position:absolute;left:111px;top:422px;width:99px;height:3px;background:var(--teal)}

.property{position:absolute;width:298px;height:285px}
.property-photo{position:absolute;left:0;top:0;width:298px;height:230px;border:2px solid var(--magenta);border-radius:18px}
.property-label{position:absolute;left:21px;top:210px;width:258px;height:72px;background:var(--white);border-radius:14px;text-align:center;padding-top:10px}
.property-label.is-hover{box-shadow:0 6px 16px rgba(0,0,0,.14)}
.property-name{font-size:21px;font-weight:500;color:var(--ink);line-height:25px}
.property-type{font-size:17px;font-weight:400;color:var(--muted);line-height:24px}
.tone-a{background:linear-gradient(180deg,#9aa3aa 0%,#8d877c 45%,#5f7046 100%)}
.tone-b{background:linear-gradient(180deg,#a9c7de 0%,#b07a5e 45%,#5e8a3d 70%,#c98e78 100%)}
.tone-c{background:linear-gradient(180deg,#6f9ec4 0%,#d8ceaa 55%,#527a3b 100%)}
.tone-d{background:linear-gradient(180deg,#6c95c2 0%,#d7ccbf 50%,#9a8a78 100%)}
.tone-e{background:linear-gradient(180deg,#8fb1d3 0%,#c8b8a2 50%,#4d7d33 100%)}
.tone-f{background:linear-gradient(180deg,#7fb0e0 0%,#c8643c 45%,#a7b09a 100%)}
.tone-g{background:linear-gradient(180deg,#6f8a5a 0%,#9b7a5a 45%,#3f7a2a 100%)}
.tone-h{background:linear-gradient(180deg,#dfe5ea 0%,#f2f2f0 55%,#6f8a4e 100%)}

.footer-line{position:absolute;left:13px;top:1822px;width:1174px;height:4px;background:linear-gradient(180deg,rgba(0,0,0,.06),rgba(0,0,0,0))}
.footer-brand{position:absolute;left:88px;top:1928px;display:flex;align-items:center;gap:9px}
.footer-brand .brand-dot{width:30px;height:30px}
.footer-brand .brand-name{font-size:20px}
.contact-list{position:absolute;left:84px;top:2033px;list-style:none;font-size:13px;color:var(--link)}
.contact-list li{display:flex;align-items:center;gap:8px;height:23px}
.contact-list svg{width:15px;height:15px;flex:none}
.social{position:absolute;left:514px;top:1880px}
.social span{display:block;width:34px;height:34px;border-radius:50%;margin-bottom:9px}
.footer-col{position:absolute;top:1868px;width:238px}
.footer-col h3{font-size:15px;font-weight:500;color:var(--ink);padding-left:16px;border-left:3px solid var(--blue);line-height:18px;height:18px;margin-bottom:14px;letter-spacing:.3px}
.footer-col ul{list-style:none;border-top:1px solid var(--rule)}
.footer-col li{font-size:13px;color:var(--link);line-height:23px;padding:6px 0 5px;border-bottom:1px solid var(--rule)}
.footer-bar{position:absolute;left:0;top:2126px;width:1200px;height:72px;background:var(--bar);color:#d8d8d8;font-size:11px;text-align:center;line-height:72px}
</style>
</head>
<body>

<header class="site-header">
  <div class="brand"><span class="brand-dot"></span><span class="brand-name">Tallowcrest Care</span></div>
  <nav class="main-nav">
    <span style="left:0">HOME</span>
    <span style="left:60px">ABOUT US</span>
    <span style="left:146px" class="active">WHAT WE DO &#8964;</span>
    <span style="left:268px">REFERRALS</span>
    <span style="left:361px">FEEDBACK</span>
    <span style="left:449px">CONTACT US</span>
  </nav>
</header>

<section class="hero">
  <div class="hero-photo" role="img" aria-label="Woman in a wheelchair sitting in a sunlit living room"></div>
  <svg class="hero-shape" width="1200" height="542" viewBox="0 0 1200 542"><polygon points="0,0 291,0 579,542 0,542" fill="#f7997b"/></svg>
  <h1 class="hero-title">Vacancies</h1>
  <div class="hero-rule"></div>
</section>

<main>
  <article class="property" style="left:111px;top:753px"><div class="property-photo tone-a" role="img" aria-label="Single storey home in Penrith with driveway and garage"></div><div class="property-label"><div class="property-name">Penrith</div><div class="property-type">4 Bedroom SIL Home</div></div></article>
  <article class="property" style="left:451px;top:753px"><div class="property-photo tone-b" role="img" aria-label="Brick home in Mount Druitt with paved driveway"></div><div class="property-label"><div class="property-name">Mount Druitt</div><div class="property-type">4 Bedroom SIL Home</div></div></article>
  <article class="property" style="left:790px;top:753px"><div class="property-photo tone-c" role="img" aria-label="Cream home in Casula with hedge garden"></div><div class="property-label"><div class="property-name">Casula</div><div class="property-type">4 Bedroom SIL Home</div></div></article>

  <article class="property" style="left:111px;top:1100px"><div class="property-photo tone-d" role="img" aria-label="Heritage home in Eastwood with shuttered windows"></div><div class="property-label"><div class="property-name">Eastwood</div><div class="property-type">4 Bedroom SIL Home</div></div></article>
  <article class="property" style="left:451px;top:1100px"><div class="property-photo tone-e" role="img" aria-label="Brick home in Baulkham Hills with palm tree and double garage"></div><div class="property-label"><div class="property-name">Baulkham Hills</div><div class="property-type">4 Bedroom SIL Home</div></div></article>
  <article class="property" style="left:790px;top:1100px"><div class="property-photo tone-f" role="img" aria-label="Orange brick home in Merrylands with wide driveway"></div><div class="property-label is-hover"><div class="property-name">Merrylands</div><div class="property-type">4 Bedroom SIL Home</div></div></article>

  <article class="property" style="left:281px;top:1448px"><div class="property-photo tone-g" role="img" aria-label="Two storey home in The Rocks with flowering garden"></div><div class="property-label"><div class="property-name">The Rocks</div><div class="property-type">4 Bedroom SIL Home</div></div></article>
  <article class="property" style="left:620px;top:1448px"><div class="property-photo tone-h" role="img" aria-label="White two storey home in Barangaroo with front fence"></div><div class="property-label"><div class="property-name">Barangaroo</div><div class="property-type">4 Bedroom SIL Home</div></div></article>
</main>

<footer>
  <div class="footer-line"></div>
  <div class="footer-brand"><span class="brand-dot"></span><span class="brand-name">Tallowcrest Care</span></div>
  <ul class="contact-list">
    <li><svg viewBox="0 0 16 16"><rect x="1.5" y="3" width="13" height="10" rx="1.5" fill="none" stroke="#e0457f" stroke-width="1.4"/><path d="M2 4l6 5 6-5" fill="none" stroke="#e0457f" stroke-width="1.4"/></svg>Email: info@tallowcrestcare.com.au</li>
    <li><svg viewBox="0 0 16 16"><path d="M4 1.5l2.5 3-1.6 1.8c.8 1.8 2.2 3.2 4 4l1.8-1.6 3 2.5-1.5 2.6C7.5 13.5 2.5 8.5 1.4 3z" fill="#e0457f"/></svg>Phone: +61 0400 318 274</li>
    <li><svg viewBox="0 0 16 16"><circle cx="8" cy="8" r="6.3" fill="none" stroke="#e0457f" stroke-width="1.4"/><path d="M8 4.5V8l2.3 1.6" fill="none" stroke="#e0457f" stroke-width="1.4"/></svg>Operating Hours: 9AM To 5PM Monday - Friday</li>
  </ul>
  <div class="social">
    <span style="background:#6b2c8f"></span>
    <span style="background:#2b4a8c"></span>
    <span style="background:#1c1c1c"></span>
    <span style="background:#0f66b0"></span>
  </div>
  <div class="footer-col" style="left:611px">
    <h3>ACCOMMODATION</h3>
    <ul>
      <li>Supported Independent Living (SIL)</li>
      <li>Specialist Disability Accommodation (SDA)</li>
      <li>Short term Accommodation (Respite)</li>
      <li>Vacancies</li>
    </ul>
  </div>
  <div class="footer-col" style="left:874px">
    <h3>WHAT WE DO</h3>
    <ul>
      <li>In Home Care</li>
      <li>Social &amp; Community Services</li>
      <li>Therapeutic Supports</li>
      <li>Support Coordination</li>
      <li>Home Modifications</li>
    </ul>
  </div>
  <div class="footer-bar">© Copyright 2024 | Tallowcrest Care | All Rights Reserved.</div>
</footer>

</body>
</html>
```